Business Cards for company that supports physicians that do medical research

Need to create a business card for Qorvel Studies (www.qorvelstudies.example), a company devoted to supporting physicians who conduct medical research. The form of the card should match the message of research and information quest. I have provided the logo of the company as an uploaded file. Designs should be simple and slick aimed at very high end clients.

Target Market(s)

Medical doctors that are also researchers

Industry/Entity Type

Medical

Contact Information for Business Card

Should feature logo and fields for personal info:
Name/title
Phone /email

Font styles to use
Serif
Sans Serif

Requirements
Must have
• Qorvel logo and fields for personal info:
• Name: Bertrand Okonfu
• Title: VP Research and Senior Analyst
• Phone: 555-203-4719
• email: info@qorvelstudies.example
Nice to have
• Interesting cards that I've seen:
• 1- all black/charcoal or very dark background
• 2- Plastic - semi-transparent
• 3- non-standard height-width ratios
• 4- Functional cards -- USB drive incorporated
Should not have
• Too busy; needs to stay very simple

```html
<!DOCTYPE html>
<html lang="en">
<head>
<meta charset="utf-8">
<title>Qorvel Studies – Business Card</title>
<link rel="stylesheet" href="https://fonts.googleapis.com/css2?family=Open+Sans:wght@400;600;700&display=swap">
<style>
  :root {
    --backdrop: #3a322d;
    --card: #0d0d0d;
    --card-edge: #1c1c1c;
    --accent-green: #6cc04a;
    --text-white: #f2f2f2;
    --silver: #b9b9b9;
    --divider: #2b3a22;
  }
  * { margin: 0; padding: 0; box-sizing: border-box; }
  html, body {
    width: 1200px; height: 900px; overflow: hidden;
    background: var(--backdrop);
    font-family: "Open Sans", Arial, sans-serif;
  }
  .canvas {
    width: 1200px; height: 900px;
    display: flex; align-items: center; justify-content: center; gap: 40px;
  }
  .card {
    width: 540px; height: 309px;
    background: var(--card);
    border: 1px solid var(--card-edge);
    box-shadow: 0 10px 30px rgba(0,0,0,0.45);
    position: relative;
  }
  .card-front { display: flex; align-items: center; }
  .brand-block {
    width: 265px; display: flex; justify-content: center; align-items: center;
  }
  .brand-name {
    font-weight: 700; font-size: 30px; line-height: 1.1;
    color: var(--accent-green); text-align: center; letter-spacing: 0.5px;
  }
  .divider {
    width: 1px; height: 130px;
    background: linear-gradient(to bottom, transparent, var(--divider), transparent);
  }
  .contact-block { padding-left: 22px; color: var(--text-white); }
  .person-name { font-weight: 600; font-size: 17px; color: var(--accent-green); }
  .person-title { font-size: 13px; margin-top: 2px; }
  .contact-list { list-style: none; margin-top: 24px; font-size: 13px; }
  .contact-list li { display: flex; align-items: center; gap: 8px; margin-bottom: 4px; }
  .contact-icon { width: 11px; height: 11px; fill: var(--accent-green); }
  .card-back { display: flex; align-items: center; justify-content: center; }
  .brand-name-back {
    font-weight: 700; font-size: 46px; line-height: 1.1;
    color: var(--silver); text-align: center; letter-spacing: 1px;
  }
</style>
</head>
<body>
<main class="canvas">
  <section class="card card-front">
    <div class="brand-block">
      <p class="brand-name">Qorvel<br>Studies</p>
    </div>
    <div class="divider"></div>
    <div class="contact-block">
      <p class="person-name">Bertrand Okonfu</p>
      <p class="person-title">VP Research and Senior Analyst</p>
      <ul class="contact-list">
        <li>
          <svg class="contact-icon" viewBox="0 0 24 24" aria-hidden="true"><path d="M6.6 10.8a15.5 15.5 0 0 0 6.6 6.6l2.2-2.2c.3-.3.7-.4 1-.2 1.1.4 2.3.6 3.6.6.6 0 1 .4 1 1V20c0 .6-.4 1-1 1A17 17 0 0 1 3 4c0-.6.4-1 1-1h3.5c.6 0 1 .4 1 1 0 1.3.2 2.5.6 3.6.1.3 0 .7-.2 1z"/></svg>
          <span>555-203-4719</span>
        </li>
        <li>
          <svg class="contact-icon" viewBox="0 0 24 24" aria-hidden="true"><path d="M2 5h20v14H2z M2 5l10 8 10-8" stroke="#0d0d0d" stroke-width="1.5"/></svg>
          <span>info@qorvelstudies.example</span>
        </li>
      </ul>
    </div>
  </section>
  <section class="card card-back">
    <p class="brand-name-back">Qorvel<br>Studies</p>
  </section>
</main>
</body>
</html>
```